Brightway Haus Inc. Business Card Design

Brightway Haus Inc. is in search of a great clean design for our business cards!

Looking to incorporate our full logo and watermark on side one (however, I am open to having the text and watermark separated within the design.)

On side two, I am looking to have contact information (Name, Position, Phone #, Email, Website (www.thebrightwayhaus.ca). Can have the logo and/or watermark as part of the design if applicable.

Please add tagline "Where Shine Counts" on either side 1 or 2. This tagline can be in a sans serif, serif or cursive font as long as it compliments overall design. Capitalization can be title or sentence case depending on how it fits within the design.

Get creative!! Looking for a clean, crisp, premium design! Looking for a glossy card finish with spot UV features when printed. Cards will also be printed with rounded corners. Standard dimensions (3.5 x 2).

Target Market(s)

B2B - primary clients are business owners or property management corporations. (residential jobs are few and far between)

Industry/Entity Type

Business

Contact Information for Business Card

- clean, crisp design
- double sided
- spot UV accents and glossy finish upon printing
- standard business card size (3.5 x 2) with rounded corners
- please see project description for requirements per side

Font styles to use
Sans Serif

Requirements
Must have
• - adequate bleeds with print ready files
• - cohesive design elements between side 1 & 2
• - spot UV elements (can be on both sides or just one, use your discretion)
• - colour pallet should match the logo file provided
• - incorporate tagline "where shine counts" (this tagline can be in a serif or sans serif font as long as it is complimentary to the overall design.
Nice to have
• - Premium elements with a clean design
Should not have
• - Please omit cartoon or whimsical like designs, think premium.
• - Colours should not stray from the pallet of the provided logo.

```html
<!DOCTYPE html>
<html lang="en">
<head>
<meta charset="utf-8">
<title>Brightway Haus Inc. Business Card</title>
<link rel="stylesheet" href="https://fonts.googleapis.com/css2?family=Open+Sans:wght@400;600;700&display=swap">
<style>
  :root {
    --backdrop: #2f2a27;
    --card: #17181a;
    --card-edge: #232427;
    --teal: #2bb3a8;
    --text-light: #e8e8e8;
    --text-muted: #a7a9ac;
    --rule: #d9d9d9;
  }
  * { box-sizing: border-box; margin: 0; padding: 0; }
  html, body {
    width: 1200px; height: 864px; overflow: hidden;
    background: var(--backdrop);
    font-family: "Open Sans", Arial, sans-serif;
  }
  .stage {
    width: 1200px; height: 864px;
    display: flex; align-items: center; justify-content: center; gap: 40px;
  }
  .card {
    position: relative;
    width: 520px; height: 297px;
    background: var(--card);
    border: 1px solid var(--card-edge);
    border-radius: 14px;
    box-shadow: 0 14px 30px rgba(0,0,0,0.45);
    overflow: hidden;
  }
  /* Side one */
  .card-front {
    display: flex; flex-direction: column; align-items: center; justify-content: center;
  }
  .brand {
    display: flex; align-items: center; gap: 12px;
    color: var(--teal); font-weight: 700; font-size: 30px; letter-spacing: 0.5px;
  }
  .brand-square { width: 26px; height: 26px; background: var(--teal); }
  .tagline {
    margin-top: 26px;
    display: flex; align-items: center; gap: 12px;
    color: var(--text-muted); font-size: 14px; letter-spacing: 0.4px;
  }
  .tagline::before, .tagline::after {
    content: ""; width: 90px; height: 1px; background: var(--text-muted);
  }
  /* Side two */
  .card-back {
    display: flex; flex-direction: column;
    padding: 56px 34px 22px;
  }
  .back-top {
    display: flex; justify-content: space-between; align-items: flex-start;
  }
  .back-brand {
    color: var(--teal); font-weight: 700; font-size: 20px; letter-spacing: 0.3px;
    line-height: 24px;
  }
  .person-name { color: var(--teal); font-weight: 700; font-size: 14px; letter-spacing: 0.6px; line-height: 18px; }
  .person-role { color: var(--text-muted); font-size: 13px; line-height: 18px; margin-top: 2px; }
  .contact-list { list-style: none; margin-top: 12px; }
  .contact-list li {
    display: flex; align-items: center; gap: 9px;
    color: var(--text-light); font-size: 12.5px; line-height: 20px;
  }
  .contact-list svg { width: 11px; height: 11px; fill: var(--teal); flex: none; }
  .divider {
    margin-top: 12px;
    height: 1px; background: var(--rule);
  }
  .address {
    margin-top: auto;
    font-style: normal;
    text-align: right; color: var(--text-light); font-size: 13px; line-height: 19px;
  }
</style>
</head>
<body>
<main class="stage">
  <section class="card card-front" aria-label="Business card front">
    <div class="brand"><span class="brand-square"></span>Brightway Haus Inc.</div>
    <p class="tagline">Where Shine Counts</p>
  </section>

  <section class="card card-back" aria-label="Business card back">
    <div class="back-top">
      <div class="person">
        <p class="person-name">ELENA MARSH</p>
        <p class="person-role">CEO/FOUNDER</p>
        <ul class="contact-list">
          <li>
            <svg viewBox="0 0 24 24" aria-hidden="true"><path d="M6.6 10.8a15.1 15.1 0 0 0 6.6 6.6l2.2-2.2c.3-.3.7-.4 1-.2 1.1.4 2.3.6 3.6.6.6 0 1 .4 1 1V20c0 .6-.4 1-1 1C10.6 21 3 13.4 3 4c0-.6.4-1 1-1h3.5c.6 0 1 .4 1 1 0 1.3.2 2.5.6 3.6.1.3 0 .7-.2 1z"/></svg>
            604 555 0182
          </li>
          <li>
            <svg viewBox="0 0 24 24" aria-hidden="true"><path d="M7 1h10a2 2 0 0 1 2 2v18a2 2 0 0 1-2 2H7a2 2 0 0 1-2-2V3a2 2 0 0 1 2-2zm0 3v14h10V4z"/></svg>
            604 555 0247
          </li>
          <li>
            <svg viewBox="0 0 24 24" aria-hidden="true"><path d="M2 5h20v14H2zm2 2v.5l8 5 8-5V7l-8 5z"/></svg>
            elena@thebrightwayhaus.ca
          </li>
        </ul>
      </div>
      <div class="back-brand">Brightway Haus Inc.</div>
    </div>
    <div class="divider"></div>
    <address class="address">
      212 Harbourview Road<br>
      Halifax, Nova Scotia B3H 1A1<br>
      www.thebrightwayhaus.ca
    </address>
  </section>
</main>
</body>
</html>
```